Modern Verdell Tree Care Website

I need a website for a full service Tree Care company. The company provides tree pruning, tree removal, tree preservation, emergency services, stump grinding, and emergency tree services.

Target Market(s)

Customers that need tree services

Industry/Entity Type

Landscaping, Tree Services

Coding

Coded - Design and coding required

Number of Pages Required

5+ page

Font styles to use
Sans Serif

Requirements
Must have
• Good clean design that showcases the services the company provides.
Nice to have
• Services page; contact form, blog, home page, about page

```html
<!DOCTYPE html>
<html lang="en">
<head>
<meta charset="utf-8">
<title>Verdell Tree Care</title>
<link rel="stylesheet" href="https://fonts.googleapis.com/css2?family=Open+Sans:wght@400;600;700&display=swap">
<style>
:root{
  --navy:#10245a;
  --navy-dark:#172f4d;
  --green:#8cc63f;
  --pale:#eef7fb;
  --text:#5f6470;
  --blue:#3b86c6;
  --white:#fff;
}
*{box-sizing:border-box;margin:0;padding:0}
html,body{width:1200px;height:4320px;overflow:hidden}
body{font-family:"Open Sans",sans-serif;color:var(--text);background:var(--white);position:relative}
.abs{position:absolute}
section,header,footer{position:absolute;left:0;width:1200px}

/* header */
.site-header{top:0;height:80px;background:var(--white);box-shadow:0 2px 6px rgba(0,0,0,.06);z-index:5}
.topbar{position:absolute;top:0;left:0;width:1200px;height:34px}
.topbar-info{position:absolute;top:9px;font-size:10px;color:#fff}
.brand{position:absolute;left:95px;top:26px;font-size:24px;font-weight:700;color:var(--navy);display:flex;align-items:center;gap:10px}
.brand-mark{width:30px;height:30px;background:var(--green)}
.nav a{position:absolute;top:50px;font-size:11px;color:#40465a;text-decoration:none}
.nav a.active{color:var(--navy);font-weight:700}

/* hero */
.hero{top:80px;height:760px;overflow:hidden}
.hero-photo{position:absolute;inset:0;background:linear-gradient(100deg,#050505 0%,#1f241c 35%,#4a5340 60%,#6a7660 80%,#56624c 100%)}
.hero h1{position:absolute;left:128px;top:182px;font-size:43px;line-height:50px;font-weight:700;color:#fff}
.hero p{position:absolute;left:129px;top:306px;width:450px;font-size:19px;line-height:28px;color:#fff}
.btn-green{position:absolute;background:var(--green);color:#fff;font-weight:700;font-size:12px;text-align:center;border:none}
.hero .btn-green{left:129px;top:420px;width:155px;height:40px;line-height:40px;border-radius:20px}

/* expertise */
.expertise{top:830px;height:570px;background:var(--pale)}
.eyebrow{position:absolute;font-size:12px;color:var(--green);text-decoration:underline;text-underline-offset:3px}
.heading{position:absolute;color:var(--navy);font-weight:700}
.center{left:0;width:1200px;text-align:center}
.intro{position:absolute;left:170px;width:860px;top:146px;font-size:13px;line-height:22px;text-align:center}
.card{position:absolute;top:254px;width:275px;height:240px;background:#fff;box-shadow:0 4px 14px rgba(0,0,0,.08);border-bottom:4px solid var(--green);text-align:center}
.card h3{position:absolute;left:0;width:100%;font-size:22px;color:#4a5262;font-weight:700}
.card p{position:absolute;left:35px;width:205px;top:90px;font-size:13px;line-height:21px}
.card svg{position:absolute;left:110px;top:60px}

/* partner */
.partner{top:1400px;height:658px}
.partner h2{left:134px;top:162px;font-size:37px;line-height:46px}
.partner h4{position:absolute;left:134px;top:282px;font-size:19px;color:#1a1f33;font-weight:600}
.partner p{position:absolute;left:134px;width:455px;font-size:12px;line-height:19px}
.btn-contact{left:134px;top:452px;width:134px;height:38px;line-height:38px;font-size:13px;font-weight:600}
.photo-round{position:absolute;border-radius:50%}

/* services */
.services{top:2058px;height:451px;display:flex}
.service-panel{position:relative;width:400px;height:451px;overflow:hidden}
.service-strip{position:absolute;top:0;right:0;width:60px;height:451px;background:rgba(23,36,80,.88)}
.strip-text{position:absolute;left:0;bottom:20px;transform-origin:left bottom;transform:translate(40px,0) rotate(-90deg);width:360px;color:#fff;font-size:11px;white-space:nowrap}
.strip-text b{font-size:15px}
.service-body{position:absolute;left:38px;top:255px;width:330px;color:#fff}
.service-body h5{font-size:15px;font-weight:700;margin-top:18px}
.service-body p{font-size:13px;line-height:21px}

/* testimonials */
.testimonials{top:2509px;height:645px;background:var(--pale)}
.testimonials .eyebrow-plain{position:absolute;top:66px;font-size:17px;color:var(--green)}
.testimonials h2{top:94px;font-size:32px;font-weight:600}
.avatar{position:absolute;border-radius:50%;border:3px solid #fff;box-shadow:0 2px 6px rgba(0,0,0,.15)}
.quote-text{position:absolute;left:290px;width:620px;top:388px;font-size:18px;line-height:31px;text-align:center;color:#2b2f3d}
.stars{position:absolute;top:508px;color:#e68a1d;font-size:17px;letter-spacing:2px}
.reviewer{position:absolute;top:533px;font-size:18px;font-weight:600;color:#e68a1d}
.role{position:absolute;top:563px;font-size:11px;color:#2b2f3d}

/* contact */
.contact{top:3154px;height:686px}
.contact h2{position:absolute;left:140px;top:122px;font-size:35px;line-height:44px;color:var(--blue);font-weight:600}
.contact h2 span{font-weight:400}
.contact .lead{position:absolute;left:140px;top:224px;width:370px;font-size:13px;line-height:22px}
.contact-line{position:absolute;left:140px;top:330px;width:380px;height:1px;background:#ddd}
.info-row{position:absolute;left:140px;display:flex;align-items:center;gap:20px;font-size:13px}
.info-icon{width:36px;height:36px;border-radius:50%;background:#fff;box-shadow:0 2px 8px rgba(0,0,0,.12);display:flex;align-items:center;justify-content:center}
.form-card{position:absolute;left:588px;top:64px;width:486px;height:544px;background:#fff;box-shadow:0 4px 18px rgba(0,0,0,.08);border-top:3px solid var(--blue);border-radius:4px}
.form-card label{position:absolute;font-size:14px;font-weight:700;color:var(--blue)}
.field{position:absolute;border:1px solid #cfd3d8;font-size:11px;color:#888;padding:13px 17px}
.form-card .btn-green{left:31px;top:450px;width:126px;height:40px;line-height:40px;font-size:13px}

/* footer */
.site-footer{top:3820px;height:500px;color:#fff}
.footer-col-title{position:absolute;top:248px;font-size:15px;font-weight:700}
.footer-row{position:absolute;font-size:11px;line-height:18px;display:flex;gap:18px;align-items:flex-start}
.footer-brand{position:absolute;left:0;width:1200px;top:200px;text-align:center;font-size:38px;font-weight:700;letter-spacing:2px}
.footer-about{position:absolute;left:447px;width:306px;top:290px;font-size:11px;line-height:21px;text-align:center}
.social{position:absolute;top:376px;width:36px;height:36px;border:1px solid #fff;background:#fff}
.hours{position:absolute;right:95px;font-size:11px;display:flex;gap:16px;align-items:center}
.footer-rule{position:absolute;left:62px;top:460px;width:1076px;height:1px;background:rgba(255,255,255,.3)}
.copyright{position:absolute;left:0;width:1200px;top:470px;text-align:center;font-size:12px}
</style>
</head>
<body>

<header class="site-header">
  <svg class="topbar" viewBox="0 0 1200 34" aria-hidden="true">
    <path d="M380 0H1200V34H430C410 34 405 0 380 0Z" fill="#1a2a3a"/>
  </svg>
  <div class="topbar-info" style="left:465px">&#9679; 48 Alder Row, Brookfield, 20417</div>
  <div class="topbar-info" style="left:705px">Follow Us: &#9632; &#9632; &#9632;</div>
  <div class="topbar-info" style="left:860px">GET QUOTATION</div>
  <div class="brand"><span class="brand-mark"></span>Verdell Tree Care</div>
  <nav class="nav">
    <a class="active" style="left:404px">Home</a>
    <a style="left:484px">Services</a>
    <a style="left:566px">About Us</a>
    <a style="left:642px">Our Team</a>
    <a style="left:717px">And more</a>
    <a style="left:791px">Contact Us</a>
  </nav>
</header>

<section class="hero">
  <div class="hero-photo" role="img" aria-label="Arborist in safety gear cutting a large tree limb"></div>
  <svg class="abs" style="left:0;top:0" width="1200" height="760" viewBox="0 0 1200 760" aria-hidden="true">
    <path d="M0 700C350 690 750 640 1200 540V760H0Z" fill="#8cc63f"/>
    <path d="M0 700C400 670 800 620 1200 545" fill="none" stroke="#8cc63f" stroke-width="0"/>
    <path d="M0 750C360 725 800 640 1200 540V760H0Z" fill="#eef7fb"/>
    <path d="M0 700Q420 665 820 655Q500 700 0 748Z" fill="#8cc63f"/>
  </svg>
  <h1>We Offer Sustainable<br>Tree Solutions</h1>
  <p>Lorem ipsum dolor sit amet, consectetur adipi scing elit, sed do eiusmod tempor incidid unt ut labore et dolore magna aliqua.</p>
  <div class="btn-green">READ MORE</div>
</section>

<section class="expertise">
  <div class="eyebrow" style="left:0;width:1200px;text-align:center;top:40px">WHO WE ARE</div>
  <h2 class="heading center" style="top:80px;font-size:40px">Your Trees, Our Expertise</h2>
  <p class="intro">Lorem ipsum dolor sit amet, consectetur adipiscing elit, sed do eiusmod tempor incididunt ut labore et dolore magna aliqua . Ut enim ad minim veniam, quis laboris nisi ut aliquip ex ea commodo consequat. Lorem ipsum dolor sit am et, consectetur adipiscing elit, sed do eiusmod te a</p>
  <div class="card" style="left:152px">
    <svg width="56" height="56" viewBox="0 0 56 56" fill="none" stroke="#8cc63f" stroke-width="2.5"><path d="M10 48H48M14 48C18 36 26 30 32 28L24 12L34 8L40 24C44 30 42 40 36 44"/></svg>
    <h3 style="top:155px">CLIENT-CENTRIC</h3>
  </div>
  <div class="card" style="left:462px">
    <h3 style="top:38px">PROFESSIONAL</h3>
    <p>Lorem ipsum dolor sit amet, consectetur adipiscing elit, se d do eiusmod tempor incidid unt ut labore et dolore magna ali</p>
  </div>
  <div class="card" style="left:768px">
    <svg width="60" height="60" viewBox="0 0 60 60" fill="none" stroke="#8cc63f" stroke-width="3"><path d="M30 8L52 24L44 50H16L8 24Z"/><circle cx="30" cy="8" r="5" fill="#fff"/><circle cx="52" cy="24" r="5" fill="#fff"/><circle cx="44" cy="50" r="5" fill="#fff"/><circle cx="16" cy="50" r="5" fill="#fff"/><circle cx="8" cy="24" r="5" fill="#fff"/></svg>
    <h3 style="top:155px">EXPERTISE</h3>
  </div>
</section>

<section class="partner">
  <div class="eyebrow" style="left:134px;top:130px;font-size:11px">WHO WE ARE</div>
  <h2 class="heading">Your Partner in Tree<br>Presevation</h2>
  <h4>Enhancing Landscapes, One Tree at a Time</h4>
  <p style="top:318px">Lorem ipsum dolor sit amet, consectetur adipiscing elit, sed do eiusmod temp or incididunt ut labore et dolore magna aliqua. Ut enim ad minim veniam, quis laboris nisi ut aliquip ex ea commodo consequat.</p>
  <p style="top:386px">Lorem ipsum dolor sit amet, consectetur adipiscing elit, sed do eiusmod temp or incididunt ut labore et dolore magna aliqua.</p>
  <div class="btn-green btn-contact">Contact us &nbsp;&rarr;</div>
  <div class="photo-round" style="left:660px;top:100px;width:430px;height:430px;background:#f0f2e2"></div>
  <div class="photo-round" role="img" aria-label="Tree trunk being cut with a red chainsaw" style="left:645px;top:91px;width:420px;height:420px;background:radial-gradient(circle at 40% 40%,#7a6a4e,#3e3a2a 70%)"></div>
  <div class="photo-round" style="left:667px;top:417px;width:94px;height:94px;background:var(--green)"></div>
  <div class="photo-round" role="img" aria-label="Climber in blue harness working high in bare trees" style="left:945px;top:133px;width:208px;height:208px;background:linear-gradient(160deg,#c9d8e8,#8f9aa6);border:4px solid #fff"></div>
</section>

<section class="services">
  <div class="service-panel">
    <div class="abs" role="img" aria-label="Gardener pruning branches with long red loppers" style="inset:0;background:linear-gradient(160deg,#6f9a4a,#3d5a2c 60%,#cfc9b8)"></div>
    <div class="service-strip"><div class="strip-text">&rarr; <b>Tree Pruning</b> &nbsp;Lorem ipsum dolor sit amet, consectetu</div></div>
  </div>
  <div class="service-panel">
    <div class="abs" role="img" aria-label="Hand resting on a freshly cut tree stump" style="inset:0;background:linear-gradient(180deg,#6d7150,#3a3a2a 55%,#1b2440)"></div>
    <div class="abs" style="inset:0;background:linear-gradient(180deg,rgba(20,30,60,0) 30%,rgba(20,30,70,.85))"></div>
    <div class="service-body">
      <svg width="56" height="56" viewBox="0 0 56 56"><circle cx="28" cy="28" r="28" fill="#fff"/><path d="M18 40H38M22 40C24 32 30 28 34 27L29 17L35 15L38 25" fill="none" stroke="#10245a" stroke-width="2"/></svg>
      <h5>Tree Removal</h5>
      <p>Lorem ipsum dolor sit amet, consectetur adipiscing elit, sed do eiusmod tempor incididunt ut labore et dolore magna aliqua. Ut enim ad minim</p>
      <p style="font-size:22px;margin-top:6px">&#10230;</p>
    </div>
  </div>
  <div class="service-panel">
    <div class="abs" role="img" aria-label="Two workers inspecting a row of hedge trees" style="inset:0;background:linear-gradient(170deg,#7e9c6a,#3f5e38 55%,#7b8a5a)"></div>
    <div class="service-strip"><div class="strip-text">&rarr; <b>Stump Grinding</b> &nbsp;Lorem ipsum dolor sit amet, consectetu</div></div>
  </div>
</section>

<section class="testimonials">
  <div class="eyebrow-plain center">TESTIMONIALS</div>
  <h2 class="heading center">What Our Clients are Saying</h2>
  <svg class="abs" style="left:0;top:0" width="1200" height="645" viewBox="0 0 1200 645" aria-hidden="true">
    <path d="M198 382Q380 220 603 231Q820 220 1009 382" fill="none" stroke="#3b86c6" stroke-width="2" stroke-dasharray="6 5"/>
    <text x="603" y="360" text-anchor="middle" font-family="Georgia,serif" font-size="90" font-weight="700" fill="#8cc63f">&#8220;</text>
  </svg>
  <div class="avatar" role="img" aria-label="Client portrait" style="left:162px;top:346px;width:72px;height:72px;background:#b9a898"></div>
  <div class="avatar" role="img" aria-label="Client portrait" style="left:346px;top:232px;width:72px;height:72px;background:#a4b3bf"></div>
  <div class="avatar" role="img" aria-label="Featured client portrait" style="left:543px;top:173px;width:120px;height:120px;background:#8e98a4"></div>
  <div class="avatar" role="img" aria-label="Client portrait" style="left:789px;top:230px;width:72px;height:72px;background:#c7b39c"></div>
  <div class="avatar" role="img" aria-label="Client portrait" style="left:973px;top:346px;width:72px;height:72px;background:#b7b0aa"></div>
  <p class="quote-text">Lorem ipsum dolor sit amet, consectetur adipiscing elit, sed do eiusmod te dunt ut labore et dolore magna aliqua .dipiscing elit, sed do eiusmod temp dunt ut labore et dolore magna aliqua .dipiscing elit, sed</p>
  <svg class="abs" style="left:466px;top:512px" width="46" height="46" viewBox="0 0 46 46"><circle cx="23" cy="23" r="22" fill="#1b2e2a"/><path d="M30 23H16M22 17L16 23L22 29" stroke="#fff" stroke-width="2" fill="none"/></svg>
  <svg class="abs" style="left:697px;top:512px" width="46" height="46" viewBox="0 0 46 46"><circle cx="23" cy="23" r="21" fill="#8cc63f" stroke="#fff" stroke-width="2"/><path d="M16 23H30M24 17L30 23L24 29" stroke="#fff" stroke-width="2" fill="none"/></svg>
  <div class="stars center">&#9733;&#9733;&#9733;&#9733;&#9733;</div>
  <div class="reviewer center">Marcus Hale</div>
  <div class="role center">Client</div>
</section>

<section class="contact">
  <h2>Get &nbsp;in Touch<br><span>Contact Us</span></h2>
  <p class="lead">Lorem ipsum dolor sit amet, consectetur adipiscing e lit, sed do eiusmod tempor incididunt ut labore et dolore magna aliqua. ceptos ...</p>
  <div class="contact-line"></div>
  <div class="info-row" style="top:358px"><span class="info-icon"><svg width="14" height="16" viewBox="0 0 14 16"><path d="M7 16C3 11 1 8 1 6A6 6 0 0 1 13 6C13 8 11 11 7 16Z" fill="#3b86c6"/><circle cx="7" cy="6" r="2" fill="#fff"/></svg></span>Lindenweg 7, 3120 Eschbach</div>
  <div class="info-row" style="top:420px"><span class="info-icon"><svg width="14" height="14" viewBox="0 0 14 14"><path d="M3 1L5 4L4 6C5 8 6 9 8 10L10 9L13 11L12 13C6 13 1 8 1 2Z" fill="#3b86c6"/></svg></span>+00 5 5501 2378</div>
  <div class="info-row" style="top:476px"><span class="info-icon"><svg width="14" height="11" viewBox="0 0 14 11"><rect width="14" height="11" rx="1" fill="#10245a"/><path d="M1 1L7 6L13 1" stroke="#fff" fill="none"/></svg></span>office@verdelltree.test</div>

  <form class="form-card">
    <label style="left:35px;top:50px">Full Name:</label>
    <div class="field" style="left:31px;top:80px;width:424px;height:42px">Sed non neque elit.</div>
    <label style="left:35px;top:154px">Email :</label>
    <label style="left:262px;top:154px">Phone no :</label>
    <div class="field" style="left:31px;top:184px;width:197px;height:42px">Sed non neque elit.</div>
    <div class="field" style="left:258px;top:184px;width:197px;height:42px">Sed non neque elit.</div>
    <label style="left:35px;top:264px">Messages :</label>
    <div class="field" style="left:31px;top:294px;width:424px;height:128px">Sed non neque elit.</div>
    <div class="btn-green">SUBMIT</div>
  </form>
</section>

<footer class="site-footer">
  <svg class="abs" style="left:0;top:0" width="1200" height="500" viewBox="0 0 1200 500" aria-hidden="true">
    <path d="M390 110Q800 30 1200 0V60Q800 70 390 110Z" fill="#8cc63f"/>
    <path d="M0 200Q500 60 1200 50V500H0Z" fill="#172f4d"/>
  </svg>
  <div class="footer-col-title" style="left:93px">CONTACT US</div>
  <div class="footer-row" style="left:93px;top:283px"><span>&#9679;</span><span>101- lorem ipsum simple text<br>print type text industry text.</span></div>
  <div class="footer-row" style="left:93px;top:340px"><span>&#9742;</span><span>555 014 2290</span></div>
  <div class="footer-row" style="left:93px;top:377px"><span>&#9993;</span><span>info@verdelltree.test</span></div>

  <div class="footer-brand">Verdell Tree Care</div>
  <p class="footer-about">Lorem ipsum dolor sit amet, consectetur adipisc ing elit, sed do eiusmod tempor incididunt dolore magna aliqua ut enim</p>
  <span class="social" style="left:535px"></span>
  <span class="social" style="left:580px"></span>
  <span class="social" style="left:625px"></span>

  <div class="footer-col-title" style="right:95px">OPENING HOURS</div>
  <div class="hours" style="top:287px">Mon - Fri: 9am - to - 6pm <span>&#9719;</span></div>
  <div class="hours" style="top:318px">Saturday 9am - to - 2pm <span>&#9719;</span></div>
  <div class="hours" style="top:349px">Sunday : <u>Closed</u> <span>&#9719;</span></div>

  <div class="footer-rule"></div>
  <div class="copyright">Verdell Tree Care</div>
</footer>

</body>
</html>
```